Business Card for Multi-Brand Sportswear Company

We are looking for a business card which represents our company and the multiple brands within it.

The company: Fen Athletics (LTD)
The brands: Fen, TavaPuni, ElmStretch, Grit and Rain

Employees using these cards would be representing Fen Athletics, rather than any of the individual brands. You will see a current design within the uploaded files, to give some inspiration. The actual text of the brands is not necessary, but the logos should be on there is some format.

Our creative minds on this are stretched, so we are looking for someone to make this their own, and show us what a good business card should look like.

We may like to get these printed with spot gloss, so keep that in mind with your designs.

www.fenathletics.co.uk

Industry/Entity Type

Business

Contact Information for Business Card

Leo Pemberton-Hale
Operations Manager
(+44) 1632 960 418
Leo@fenathletics.co.uk
www.fenathletics.co.uk

Font styles to use
Sans Serif
Other font styles liked:
• Eurostile

Colors
ffffff

Requirements
Nice to have
• Dark (black) background

```html
<!DOCTYPE html>
<html lang="en">
<head>
<meta charset="utf-8">
<title>Fen Athletics – Business Card</title>
<link rel="stylesheet" href="https://fonts.googleapis.com/css2?family=Exo+2:wght@400;500;600;700&display=swap">
<style>
  :root {
    --page-bg: #ececec;
    --card-light-a: #ffffff;
    --card-light-b: #e4e4e4;
    --card-dark-a: #353535;
    --card-dark-b: #242424;
    --ink-dark: #111111;
    --ink-light: #ffffff;
    --ink-muted: #d8d8d8;
    --accent-red: #d42a2a;
    --brand-font: "Exo 2", sans-serif;
  }
  * { box-sizing: border-box; margin: 0; padding: 0; }
  html, body {
    width: 1200px;
    height: 586px;
    overflow: hidden;
    background: var(--page-bg);
    font-family: var(--brand-font);
  }
  .canvas {
    position: relative;
    width: 1200px;
    height: 586px;
  }
  .card {
    position: absolute;
    top: 130px;
    width: 500px;
    height: 300px;
    overflow: hidden;
  }
  .card--front { left: 66px; }
  .card--back  { left: 608px; color: var(--ink-light); }
  .card__texture {
    position: absolute;
    inset: 0;
  }
  .card--front .card__texture {
    background: linear-gradient(135deg, var(--card-light-a) 0%, var(--card-light-b) 50%, var(--card-light-a) 100%);
  }
  .card--back .card__texture {
    background: linear-gradient(135deg, var(--card-dark-a) 0%, var(--card-dark-b) 55%, var(--card-dark-a) 100%);
  }
  .wordmark {
    position: absolute;
    display: flex;
    flex-direction: column;
    align-items: flex-end;
    font-family: var(--brand-font);
  }
  .wordmark__name {
    font-weight: 600;
    letter-spacing: 0.5px;
    line-height: 1;
  }
  .wordmark__tagline {
    font-weight: 400;
    letter-spacing: 2px;
    line-height: 1;
    margin-top: 4px;
  }
  .card--front .wordmark {
    left: 0; right: 0;
    top: 130px;
    align-items: center;
    color: var(--ink-dark);
  }
  .card--front .wordmark__name { font-size: 44px; }
  .card--front .wordmark__tagline { font-size: 11px; margin-top: 6px; align-self: center; padding-left: 150px; }
  .card--back .wordmark {
    left: 0; right: 0;
    top: 42px;
    align-items: center;
  }
  .card--back .wordmark__name { font-size: 30px; }
  .card--back .wordmark__tagline { font-size: 8px; padding-left: 120px; }

  .holder {
    position: absolute;
    right: 32px;
    top: 142px;
    text-align: right;
  }
  .holder__name {
    font-size: 17px;
    font-weight: 600;
    line-height: 20px;
  }
  .holder__title {
    font-size: 12px;
    font-weight: 400;
    line-height: 14px;
    margin-top: 3px;
  }
  .divider {
    position: absolute;
    left: 26px;
    top: 170px;
    width: 334px;
    height: 3px;
    background: var(--accent-red);
  }
  .contact {
    position: absolute;
    left: 30px;
    top: 186px;
    list-style: none;
  }
  .contact__item {
    display: flex;
    align-items: center;
    gap: 8px;
    height: 24.5px;
    font-size: 11.5px;
    color: var(--ink-muted);
  }
  .contact__icon { width: 14px; height: 12px; fill: var(--accent-red); }
  .address {
    position: absolute;
    left: 31px;
    top: 259px;
    font-size: 12px;
    font-weight: 600;
    font-style: normal;
  }
  .brand-row {
    position: absolute;
    right: 28px;
    top: 258px;
    display: flex;
    gap: 10px;
    list-style: none;
    font-size: 9.5px;
    font-weight: 500;
    color: var(--ink-muted);
  }
</style>
</head>
<body>
<main class="canvas">

  <section class="card card--front" aria-label="Business card front">
    <div class="card__texture" role="img" aria-label="Light faceted low-poly background texture"></div>
    <div class="wordmark">
      <span class="wordmark__name">Fen Athletics</span>
      <span class="wordmark__tagline">PERFORMANCE WEAR</span>
    </div>
  </section>

  <section class="card card--back" aria-label="Business card back">
    <div class="card__texture" role="img" aria-label="Dark faceted low-poly background texture"></div>
    <div class="wordmark">
      <span class="wordmark__name">Fen Athletics</span>
      <span class="wordmark__tagline">PERFORMANCE WEAR</span>
    </div>

    <div class="holder">
      <p class="holder__name">Hugo Ashdown</p>
      <p class="holder__title">Managing Director</p>
    </div>
    <div class="divider"></div>

    <ul class="contact">
      <li class="contact__item">
        <svg class="contact__icon" viewBox="0 0 14 12" aria-hidden="true"><path d="M1 3.5C1 2 2.5 1 7 1s6 1 6 2.5V5h-3V3.8H4V5H1z"/><path d="M3 6h8l1.5 5h-11z"/></svg>
        <span>+44 (0)1632 960527</span>
      </li>
      <li class="contact__item">
        <svg class="contact__icon" viewBox="0 0 14 12" aria-hidden="true"><rect x="3.5" y="0.5" width="7" height="3"/><rect x="0.5" y="4" width="13" height="5" rx="1"/><rect x="3.5" y="8" width="7" height="3.5"/></svg>
        <span>(555) 014-2290</span>
      </li>
      <li class="contact__item">
        <svg class="contact__icon" viewBox="0 0 14 12" aria-hidden="true"><path d="M0.5 1.5h13v9h-13z"/><path d="M1 2l6 5 6-5" fill="none" stroke="#242424" stroke-width="1.2"/></svg>
        <span>hugo@fenathletics.co.uk</span>
      </li>
    </ul>

    <address class="address">Marsh Lane, Eldon Fenby, YO9 4QT</address>

    <ul class="brand-row" aria-label="Group brands">
      <li>TavaPuni</li>
      <li>Grit and Rain</li>
      <li>ElmStretch</li>
      <li>Fen</li>
    </ul>
  </section>

</main>
</body>
</html>
```